NZ First of it's kind solutions directory and marketplace for busy Mums needs a business card design

We need a business card design for our new nationwide business in NZ (long term plans to go global). We provide solutions to the everyday challenges that busy Mums face by connecting them with quality communities and suppliers of carefully selected, relevant products and services. We sell direct via our online marketplace. The final design should communicate our values of inclusivity, quality and smart solutions. Colours should incorporate our logo colour palette of #477077 and #6ba8b2. Our website is at https://www.brightnestmums.example

Target Market(s)

busy Mums, Age 28 – 50, female, income over $100K, location main centres NZ primarily but NZ wide. Is likely juggling work or career with a young family. Probably had hobbies which have fallen by the wayside.
-Wants to succeed in her chosen career without compromising on family life
-to successfully juggle her career without feeling like she is compromising her children
- Is time poor, something always has to give and it’s generally her health (she’ll stay up late, get stressed)
- probably ex corporate or professional career. Has discretional income

Industry/Entity Type

Business

Contact Information for Business Card

Lena Forbisher, Founder, BrightNestMums.example (Strapline Tap; Gather; Sorted), 47 Kowhai Terrace, Ellerslie, Auckland 1051, New Zealand. Mob: 021 483 517 Ph: +64 (0)9 571 4860

Font styles to use
Other font styles liked:
• Raleway, and/or Architects Daughter

Colors
00a990
33b8a4
86cfc6
cfeae6

Requirements
Must have
• the above details, streamline. the logo and colours associated with those logos
Should not have
• foil or metallic colours

```html
<!DOCTYPE html>
<html lang="en">
<head>
<meta charset="utf-8">
<title>BrightNestMums business card</title>
<link href="https://fonts.googleapis.com/css2?family=Nunito:wght@700&family=Roboto:ital,wght@0,400;1,400&display=swap" rel="stylesheet">
<style>
  :root {
    --backdrop: #e3e3e3;
    --card: #f7f7f7;
    --teal-deep: #3b5e66;
    --teal: #477077;
    --teal-light: #6ba8b2;
    --ink: #3c3c3c;
    --ghost: #c4cbcd;
  }
  html, body {
    margin: 0;
    width: 1200px;
    height: 576px;
    overflow: hidden;
    background: var(--backdrop);
  }
  .stage { position: relative; width: 1200px; height: 576px; }
  .card {
    position: absolute;
    top: 138px;
    height: 294px;
    background: var(--card);
    border-radius: 14px;
    overflow: hidden;
    box-shadow: 0 3px 8px rgba(0,0,0,0.18);
  }
  .card--front { left: 82px; width: 484px; }
  .card--back { left: 602px; width: 481px; height: 292px; }

  .front-disc {
    position: absolute;
    left: 10px; top: 115px;
    width: 182px; height: 182px;
    border-radius: 50%;
    background: var(--teal-deep);
  }
  .brand-name {
    position: absolute;
    font-family: "Nunito", sans-serif;
    font-weight: 700;
    color: var(--teal);
    white-space: nowrap;
    margin: 0;
    letter-spacing: -0.5px;
  }
  .card--front .brand-name { left: 212px; top: 198px; font-size: 33px; }
  .strapline {
    position: absolute;
    left: 213px; top: 250px;
    margin: 0;
    font-family: "Roboto", sans-serif;
    font-size: 11px;
    letter-spacing: 3.6px;
    color: var(--ink);
    white-space: nowrap;
  }
  .strapline .divider { color: var(--teal-light); padding: 0 4px; }

  .holder-name {
    position: absolute; left: 22px; top: 44px; margin: 0;
    font-family: "Nunito", sans-serif; font-weight: 700;
    font-size: 19px; color: var(--teal-deep);
  }
  .holder-role {
    position: absolute; left: 23px; top: 68px; margin: 0;
    font-family: "Roboto", sans-serif; font-style: italic;
    font-size: 11.5px; color: var(--ink);
  }
  .back-brand {
    position: absolute; right: 20px; top: 44px;
    display: flex; align-items: center; gap: 7px;
  }
  .back-brand .brand-mark {
    width: 24px; height: 24px; border-radius: 50%;
    background: var(--teal-deep);
  }
  .back-brand .brand-name { position: static; font-size: 23px; }
  .ghost-disc {
    position: absolute; left: 330px; top: 180px;
    width: 160px; height: 160px; border-radius: 50%;
    background: var(--ghost);
  }
  .address {
    position: absolute; left: 26px; top: 155px; margin: 0;
    font-family: "Roboto", sans-serif; font-style: normal;
    font-size: 11.5px; line-height: 18px; color: var(--ink);
  }
  .contacts {
    position: absolute; left: 26px; top: 202px;
    list-style: none; margin: 0; padding: 0;
    font-family: "Roboto", sans-serif; font-size: 11.5px; color: var(--ink);
  }
  .contacts li { display: flex; align-items: center; height: 18px; }
  .contacts svg { width: 11px; height: 11px; margin-right: 10px; fill: var(--teal); }
</style>
</head>
<body>
<main class="stage">

  <section class="card card--front" aria-label="Card front">
    <div class="front-disc"></div>
    <p class="brand-name">BrightNestMums</p>
    <p class="strapline">TAP<span class="divider">|</span>GATHER<span class="divider">|</span>SORTED</p>
  </section>

  <section class="card card--back" aria-label="Card back">
    <div class="ghost-disc"></div>
    <h1 class="holder-name">Lena Forbisher</h1>
    <p class="holder-role">Founder</p>
    <div class="back-brand">
      <span class="brand-mark"></span>
      <p class="brand-name">BrightNestMums</p>
    </div>
    <address class="address">47 Kowhai Terrace, Ellerslie,<br>Auckland 1051, New Zealand</address>
    <ul class="contacts">
      <li><svg viewBox="0 0 12 12" aria-hidden="true"><rect x="3" y="0.5" width="6" height="11" rx="1"/><rect x="4" y="2" width="4" height="7" fill="#f7f7f7"/></svg>021 483 517</li>
      <li><svg viewBox="0 0 12 12" aria-hidden="true"><path d="M1 4c0-2 2-3 5-3s5 1 5 3H8.5V3h-5v1z"/><path d="M2.5 5h7l1.5 6H1z"/></svg>+64 (0)9 571 4860</li>
      <li><svg viewBox="0 0 12 12" aria-hidden="true"><rect x="0.5" y="2" width="11" height="8"/><path d="M0.5 2L6 7l5.5-5" stroke="#f7f7f7" fill="none"/></svg>www.BrightNestMums.example</li>
      <li><svg viewBox="0 0 12 12" aria-hidden="true"><circle cx="6" cy="6" r="5.5"/><path d="M0.5 6h11M6 0.5v11M2 3h8M2 9h8" stroke="#f7f7f7" stroke-width="0.8" fill="none"/></svg>lena@brightnestmums.example</li>
    </ul>
  </section>

</main>
</body>
</html>
```